Kelvaro.ch is looking for business card letterhead and envelope C5 with WOW effect

We need a strong business card for our company Kelvaro.ch, logo is available. You want a black or dark background on which the logo Stark r% 26 # 252; appears. Letterhead and envelope in C5 format should be in a similar design, but does not have to be We need a strong business card for our company Kelvaro.ch, logo is available. A black or dark background is desired, on which the logo Stark comes across. The letterhead and the envelope in C5 format should have a similar design.

Target Market(s)

Private customers as well as entrepreneurs

Contact Information for Business Card

E-mail: info@kelvaro-example.ch
Web.www.Kelvaro-example.ch
Tel: +41 ( 0 ) 79 482 6037
Adresse:
Lindenweg 14
9406 Tarnbach

Hier kann man Icons verwenden für Email,Tel und Adressse

Font styles to use
Other font styles liked:
• Dubai,bold

Colors

Designer to choose colors to be used in the design.

Requirements
Must have
• WOW effect
Nice to have
• R% 26 # 252; back business card with our service listings. - VEHICLE LABELING - SHOP WINDOW LABELING - STICKERS AND MUCH MORE ... in red color

```html
<!DOCTYPE html>
<html lang="en">
<head>
<meta charset="utf-8">
<title>Kelvaro.ch – Business Card</title>
<link href="https://fonts.googleapis.com/css2?family=Exo+2:wght@600;700&family=Montserrat:wght@400;500;600&display=swap" rel="stylesheet">
<style>
  :root {
    --stage: #2b2b2d;
    --card: #1c1d1f;
    --yellow: #f8c51b;
    --yellow-strong: rgba(248, 197, 27, 0.95);
    --yellow-mid: rgba(248, 197, 27, 0.6);
    --yellow-faint: rgba(248, 197, 27, 0.12);
    --yellow-glow: rgba(248, 197, 27, 0.06);
    --white: #f4f4f4;
    --silver: #a4a6a9;
  }
  * { margin: 0; padding: 0; box-sizing: border-box; }
  html, body { width: 1200px; height: 874px; overflow: hidden; }
  body {
    background: var(--stage);
    position: relative;
    font-family: "Montserrat", Arial, sans-serif;
    color: var(--white);
  }
  .card {
    position: absolute;
    left: 300px;
    width: 600px;
    height: 350px;
    background: var(--card);
    overflow: hidden;
  }
  .card--back { top: 60px; }
  .card--front { top: 464px; }

  /* Back side */
  .hex-field {
    position: absolute;
    left: -140px; top: -90px;
    width: 620px; height: 530px;
    background: radial-gradient(closest-side ellipse at 50% 50%,
      var(--yellow-strong) 0%,
      var(--yellow-mid) 38%,
      var(--yellow-faint) 72%,
      transparent 100%);
  }
  .back-brand {
    position: absolute;
    right: 42px; top: 108px;
    font-family: "Exo 2", Arial, sans-serif;
    font-weight: 700;
    font-size: 44px;
    letter-spacing: 1px;
    color: var(--silver);
    text-transform: uppercase;
  }
  .services {
    position: absolute;
    right: 42px; top: 176px;
    list-style: none;
    text-align: right;
  }
  .services li {
    font-size: 14px;
    font-weight: 500;
    letter-spacing: 0.5px;
    line-height: 22px;
    text-transform: uppercase;
    color: var(--white);
  }
  .services li::after {
    content: "";
    display: inline-block;
    width: 5px; height: 5px;
    border-radius: 50%;
    background: var(--yellow);
    margin-left: 8px;
    vertical-align: middle;
  }

  /* Front side */
  .network {
    position: absolute;
    left: 80px; top: -40px;
    width: 620px; height: 420px;
    background: radial-gradient(closest-side ellipse at 55% 55%,
      var(--yellow-faint) 0%,
      var(--yellow-glow) 55%,
      transparent 100%);
  }
  .front-brand {
    position: absolute;
    left: 58px; top: 58px;
    display: flex;
    align-items: center;
    gap: 16px;
  }
  .front-brand__mark {
    width: 46px; height: 46px;
    background: var(--yellow);
  }
  .front-brand__name {
    font-family: "Exo 2", Arial, sans-serif;
    font-weight: 700;
    font-size: 30px;
    color: var(--white);
    text-transform: uppercase;
  }
  .person {
    position: absolute;
    left: 58px; top: 168px;
  }
  .person__name {
    font-family: "Exo 2", Arial, sans-serif;
    font-weight: 700;
    font-size: 27px;
    color: var(--yellow);
    line-height: 30px;
  }
  .person__role {
    font-size: 15px;
    font-weight: 500;
    margin-bottom: 10px;
  }
  .person__line {
    font-size: 14px;
    line-height: 22px;
    color: var(--white);
  }
  .web {
    position: absolute;
    right: 42px; bottom: 38px;
  }
  .web p {
    font-size: 15px;
    line-height: 24px;
    color: var(--white);
  }
  .accent-strip {
    position: absolute;
    left: 0; bottom: 0;
    width: 100%; height: 6px;
    background: var(--yellow);
  }
</style>
</head>
<body>

  <section class="card card--back" aria-label="Card back">
    <div class="hex-field" role="img" aria-label="Yellow and black honeycomb hexagon pattern"></div>
    <p class="back-brand">Kelvaro.ch</p>
    <ul class="services">
      <li>Vehicle labeling</li>
      <li>Shop window labeling</li>
      <li>Stickers</li>
    </ul>
  </section>

  <section class="card card--front" aria-label="Card front">
    <div class="network" role="img" aria-label="Faint golden geometric network of lines"></div>
    <div class="front-brand">
      <span class="front-brand__mark"></span>
      <span class="front-brand__name">Kelvaro.ch</span>
    </div>
    <div class="person">
      <p class="person__name">Jonas Brenner</p>
      <p class="person__role">President</p>
      <p class="person__line">+41 ( 0 ) 79 482 6037</p>
      <p class="person__line">Lindenweg 14 9406 Tarnbach</p>
    </div>
    <div class="web">
      <p>info@kelvaro-example.ch</p>
      <p>www.Kelvaro-example.ch</p>
    </div>
    <div class="accent-strip"></div>
  </section>

</body>
</html>
```